Harborline Auto LLC

Car Dealer Customer Service
Address: 2874 Cresthaven Road, Shelbyville, TN 37162
web: www.harborlineautoxq.net
email: harborlineautoxq@mailnest.example
Phone: (931) 555-0148
Phone: (629) 555-0173

```html
<!DOCTYPE html>
<html lang="en">
<head>
<meta charset="utf-8">
<title>Harborline Auto – Business Card</title>
<link rel="stylesheet" href="https://fonts.googleapis.com/css2?family=Poppins:wght@400;600;700&family=Roboto:wght@400;500&display=swap">
<style>
  :root {
    --stage: #2b2f36;
    --card-dark: #1c1c1c;
    --card-light: #ffffff;
    --gold: #f0ad3a;
    --blue: #2a8fd4;
    --ink: #111111;
    --muted: #6d6d6d;
    --white: #ffffff;
  }
  * { margin: 0; padding: 0; box-sizing: border-box; }
  html, body { width: 1200px; height: 781px; overflow: hidden; }
  body {
    background: var(--stage);
    font-family: "Poppins", sans-serif;
    position: relative;
  }
  .card {
    position: absolute;
    top: 241px;
    width: 520px;
    height: 298px;
    overflow: hidden;
    box-shadow: 0 14px 30px rgba(0,0,0,.45);
  }
  /* Back side */
  .card-back { left: 50px; background: var(--card-dark); }
  .back-brand {
    position: absolute;
    left: 0; right: 0; top: 78px;
    display: flex; flex-direction: column; align-items: center;
  }
  .back-mark {
    width: 74px; height: 74px; border-radius: 50%;
    background: var(--gold);
    margin-bottom: 16px;
  }
  .back-name {
    color: var(--white);
    font-weight: 700;
    font-size: 30px;
    letter-spacing: 1px;
    line-height: 1;
  }
  .back-tagline {
    margin-top: 8px;
    color: var(--white);
    font-family: "Roboto", sans-serif;
    font-size: 12.5px;
    letter-spacing: 1.2px;
  }
  /* Front side */
  .card-front { left: 630px; background: var(--card-light); }
  .card-front .shapes { position: absolute; inset: 0; }
  .front-brand {
    position: absolute; left: 42px; top: 66px;
    display: flex; align-items: center; gap: 10px;
  }
  .front-mark { width: 30px; height: 30px; border-radius: 50%; background: var(--blue); }
  .front-name {
    color: var(--blue); font-weight: 700; font-size: 17px; line-height: 1.05;
    text-transform: uppercase;
  }
  .divider {
    position: absolute; left: 262px; top: 118px;
    width: 2px; height: 64px; background: var(--blue);
  }
  .person { position: absolute; left: 280px; top: 118px; }
  .person-name { font-size: 21px; color: var(--ink); font-weight: 400; line-height: 1.1; }
  .person-name strong { font-weight: 700; }
  .person-role { font-size: 13px; color: var(--muted); }
  .contacts {
    position: absolute; left: 232px; top: 192px;
    list-style: none;
    font-family: "Roboto", sans-serif; font-size: 9.5px; color: var(--ink);
  }
  .contacts li { display: flex; align-items: center; gap: 7px; height: 14px; white-space: nowrap; }
  .contacts svg { width: 8px; height: 8px; flex: none; }
</style>
</head>
<body>
  <section class="card card-back" aria-label="Card back">
    <div class="back-brand">
      <div class="back-mark"></div>
      <div class="back-name">HARBORLINE AUTO</div>
      <div class="back-tagline">CAR DEALER CUSTOMER SERVICE</div>
    </div>
  </section>

  <section class="card card-front" aria-label="Card front">
    <svg class="shapes" viewBox="0 0 520 298" aria-hidden="true">
      <polygon points="0,256 360,256 344,276 0,276" fill="var(--blue)"/>
      <polygon points="344,276 360,256 520,248 520,298 330,298" fill="var(--ink)"/>
    </svg>
    <div class="front-brand">
      <div class="front-mark"></div>
      <div class="front-name">Harborline<br>Auto</div>
    </div>
    <div class="divider"></div>
    <div class="person">
      <div class="person-name">PERSON <strong>NAME</strong></div>
      <div class="person-role">President</div>
    </div>
    <ul class="contacts">
      <li>
        <svg viewBox="0 0 10 10"><circle cx="5" cy="5" r="4" fill="none" stroke="currentColor" stroke-width="1.4"/><line x1="1" y1="5" x2="9" y2="5" stroke="currentColor"/></svg>
        www.harborlineautoxq.net
      </li>
      <li>
        <svg viewBox="0 0 10 10"><rect x="0.5" y="2" width="9" height="6" fill="currentColor"/><polyline points="0.5,2 5,6 9.5,2" fill="none" stroke="#fff" stroke-width="0.8"/></svg>
        harborlineautoxq@mailnest.example
      </li>
      <li>
        <svg viewBox="0 0 10 10"><path d="M2 1 L4 1 L4.6 3.4 L3.4 4.3 Q4.4 6.2 5.8 6.7 L6.7 5.5 L9 6.1 L9 8.2 Q5 9.4 1.6 5 Q0.6 2.8 2 1Z" fill="currentColor"/></svg>
        (931) 555-0148, (629) 555-0173
      </li>
    </ul>
  </section>
</body>
</html>
```